Recruitment of Trellan Staffing for the UK market

I want a website for the UK market to attract businesses and companies to come to us for Philipine labour. We want an information site that gives all information on what we do and how we can recruit Philippine labour.
This is a recruitment site for companies to contact us with their requirements for skilled workers coming from the Philipines over to the UK to work.

Target Market(s)

Uk Companies and businesses who want Philipine skilled workers

Industry/Entity Type

REcruitment

Coding

Number of Pages Required

5+ page

Font styles to use
Sans Serif

Colors
0054AA
0677BA
7BADD7
CADEEF
E8F1F8
0094D4
00A9DD
6FCCEA
C7EBF8
E9F6FB
EE7325
F08F49
F5BC92
FAE3D3
FDF4ED
EB3D1F
EC4F4E
F09395
F8D3D4
FCEDEE

Requirements
Must have
• Look professional and corperate with drop down menus for Home ,about, services,articles. training , contact us
Nice to have
• Look at Velmora recruitment- https://velmorarecruitment.example.co.uk/. This is my current site - https://www.trellanstaffing.example.com/
Should not have
• Cartoons or silly pictures , needs to be corperate looking

```html
<!DOCTYPE html>
<html lang="en">
<head>
<meta charset="utf-8">
<title>Trellan Staffing – Philippine Skilled Workers for UK Companies</title>
<link href="https://fonts.googleapis.com/css2?family=Montserrat:wght@400;500;600;700&family=Oswald:wght@500&display=swap" rel="stylesheet">
<style>
:root{
  --blue:#0054AA;
  --blue-mid:#0677BA;
  --orange:#EE7325;
  --orange-pale:#FAE3D3;
  --red:#EB3D1F;
  --ink:#1e1e1e;
  --text:#3a3a3a;
  --muted:#8a8a8a;
  --line:#d6d6d6;
  --grey-bg:#f3f3f3;
  --white:#ffffff;
}
*{margin:0;padding:0;box-sizing:border-box}
html,body{width:1200px;height:5259px;overflow:hidden}
body{font-family:"Montserrat",sans-serif;color:var(--text);background:var(--white);position:relative}
.section{position:absolute;left:0;width:1200px}
.abs{position:absolute}
.btn{position:absolute;display:flex;align-items:center;justify-content:center;background:var(--blue);color:var(--white);font-size:11px;font-weight:600;text-decoration:none}
.h2{font-size:30px;font-weight:500;color:var(--ink);line-height:40px}
.rule{position:absolute;height:3px;width:42px;background:var(--orange)}
.photo{position:absolute}

/* header */
.site-header{top:0;height:76px;background:var(--white)}
.brand{left:163px;top:22px;font-size:22px;font-weight:700;color:#8e2a2a;letter-spacing:.2px}
.brand-mark{display:inline-block;width:14px;height:14px;background:#8e2a2a;margin-right:8px;vertical-align:1px}
.head-contact{top:28px;font-size:13px;color:#555;display:flex;align-items:center;gap:6px}
.menu-btn{left:996px;top:16px;width:42px;height:43px;background:var(--red);display:flex;align-items:center;justify-content:center}

/* hero */
.hero{top:76px;height:587px}
.hero-photo{left:0;top:0;width:1200px;height:587px;background:linear-gradient(100deg,#1f2733 0%,#3b4656 40%,#6f7a86 70%,#4a5462 100%)}
.hero-title{left:163px;top:305px;font-family:"Oswald",sans-serif;font-size:38px;line-height:49px;color:var(--white);font-weight:500}
.hero-title span{color:var(--red)}
.form-card{left:686px;top:179px;width:353px;height:463px;background:var(--white);box-shadow:0 10px 30px rgba(0,0,0,.12)}
.form-card h3{position:absolute;left:0;width:100%;top:38px;text-align:center;font-family:"Oswald",sans-serif;font-weight:500;font-size:29px;color:var(--red)}
.field{position:absolute;left:32px;width:288px;height:37px;border:1px solid #9a9a9a;font-size:11px;color:#777;padding:10px 12px 0 34px}
.field svg{position:absolute;left:14px;top:11px}
.send-btn{left:108px;top:378px;width:136px;height:36px;background:var(--red);font-weight:500}

/* about */
.about{top:767px;height:521px;background:var(--grey-bg)}
.about-photo{left:163px;top:39px;width:392px;height:392px;border-radius:50%;background:radial-gradient(circle at 45% 40%,#e9eef3 0%,#b9c6d2 55%,#5d6c7c 100%)}
.about-dot{left:487px;top:302px;width:90px;height:90px;border-radius:50%;background:#d9d9d9}
.about h2{left:633px;top:105px;width:380px}
.about p{position:absolute;left:633px;top:212px;width:400px;font-size:11px;line-height:23px;color:#333}

/* working */
.working{top:1288px;height:538px}
.working h2{left:163px;top:133px}
.working p{position:absolute;left:163px;top:207px;width:380px;font-size:16px;line-height:34px;color:#333}
.working p b{color:var(--red);text-decoration:underline}
.map{left:633px;top:59px;width:377px;height:388px;background:linear-gradient(160deg,#eef4f9 0%,#d5e2ee 100%);border-radius:6px}

/* services */
.services{top:1826px;height:545px;background:var(--grey-bg)}
.svc-card{position:absolute;top:92px;width:260px;height:288px;background:var(--white);box-shadow:0 2px 8px rgba(0,0,0,.06);text-align:center}
.svc-card svg{margin-top:32px}
.svc-card h3{font-size:16px;font-weight:600;color:var(--ink);margin-top:34px}
.svc-card p{font-size:11px;line-height:23px;color:#444;margin:12px auto 0;width:200px}

/* placement */
.placement{top:2371px;height:558px}
.center-title{left:0;width:1200px;text-align:center}
.place-tile{position:absolute;top:166px;height:228px;display:flex;align-items:center;justify-content:center;font-size:19px;font-weight:700;color:var(--white);text-shadow:0 1px 3px rgba(0,0,0,.5)}
.arrow-btn{position:absolute;top:260px;width:42px;height:40px;border:1px solid #cfcfcf;background:var(--white);display:flex;align-items:center;justify-content:center}

/* testimonial */
.testimonial{top:2929px;height:489px;background:var(--grey-bg)}
.t-card{left:441px;top:91px;width:598px;height:309px;background:var(--white);box-shadow:0 2px 10px rgba(0,0,0,.05)}
.t-photo{left:163px;top:112px;width:323px;height:267px;background:linear-gradient(180deg,#6f7680 0%,#a8b0b8 45%,#e6e9ec 100%)}
.stars{left:543px;top:124px;display:flex;gap:4px}
.t-quote{left:543px;top:160px;width:420px;font-size:15px;line-height:28px;color:#333}
.t-name{left:543px;top:328px;font-size:17px;font-weight:600;color:var(--blue)}
.t-role{left:543px;top:352px;font-size:11px;color:var(--muted)}
.t-mark{left:958px;top:334px;font-family:Georgia,serif;font-size:90px;line-height:90px;color:var(--orange-pale);font-weight:700}

/* info cards */
.info{top:3418px;height:456px}
.info-card{position:absolute;top:129px;width:270px;height:235px;border:1px solid #cfcfcf;background:var(--white);text-align:center}
.info-icon{position:absolute;left:98px;top:-36px;width:74px;height:74px;border-radius:50%;background:var(--white);border:1px solid #d8d8d8;display:flex;align-items:center;justify-content:center}
.info-card h3{font-size:16px;font-weight:600;color:var(--ink);margin-top:54px}
.info-card p{font-size:11px;line-height:23px;color:#444;width:220px;margin:10px auto 0}
.info-card .btn{left:78px;top:171px;width:114px;height:36px}

/* contact banner */
.banner{top:3874px;height:447px}
.banner-photo{left:0;top:0;width:1200px;height:447px;background:linear-gradient(90deg,#1c1d1f 0%,#2c2d30 45%,#4a4d57 70%,#2d3f6a 100%)}
.banner h2{left:163px;top:90px;color:var(--white);font-size:32px;font-weight:500}
.banner .rule{left:163px;top:138px}
.banner p{position:absolute;left:163px;top:160px;width:400px;font-size:11px;line-height:23px;color:#f0f0f0}
.banner .btn{left:161px;top:314px;width:111px;height:34px;background:var(--white);color:var(--blue)}

/* quick contact */
.quick{top:4321px;height:602px}
.qf{position:absolute;width:290px}
.qf label{display:block;font-size:10px;color:#999}
.qf .val{font-size:11px;color:#333;margin-top:17px;padding-bottom:9px;border-bottom:1px solid var(--line);position:relative}
.qf svg{position:absolute;right:4px;top:-4px}

/* footer */
.site-footer{top:4923px;height:292px;background:var(--blue);color:var(--white)}
.site-footer h4{position:absolute;top:72px;font-size:15px;font-weight:600}
.f-link{position:absolute;font-size:12px}
.f-item{position:absolute;left:467px;font-size:12px;line-height:19px}
.f-icon{position:absolute;left:440px}
.social{position:absolute;top:5px;width:27px;height:27px;border:1.5px solid var(--white);border-radius:50%}
.f-brand{left:798px;top:188px;font-size:22px;font-weight:700;color:var(--white)}
.copy-bar{top:5215px;height:44px;background:var(--orange);color:var(--white);font-size:11px;text-align:center;line-height:44px}
</style>
</head>
<body>

<header class="section site-header">
  <div class="abs brand"><span class="brand-mark"></span>Trellan Staffing</div>
  <div class="abs head-contact" style="left:606px">
    <svg width="16" height="16" viewBox="0 0 24 24" fill="none" stroke="#EB3D1F" stroke-width="2"><path d="M22 16.9v3a2 2 0 0 1-2.2 2 19.8 19.8 0 0 1-8.6-3.1 19.5 19.5 0 0 1-6-6A19.8 19.8 0 0 1 2.1 4.2 2 2 0 0 1 4.1 2h3a2 2 0 0 1 2 1.7c.1 1 .4 1.9.7 2.8a2 2 0 0 1-.5 2.1L8 9.9a16 16 0 0 0 6 6l1.3-1.3a2 2 0 0 1 2.1-.4c.9.3 1.8.6 2.8.7a2 2 0 0 1 1.7 2z"/></svg>
    07700 900418
  </div>
  <div class="abs head-contact" style="left:750px;font-size:12px">
    <svg width="16" height="16" viewBox="0 0 24 24" fill="none" stroke="#EB3D1F" stroke-width="2"><rect x="2" y="4" width="20" height="16" rx="2"/><path d="M2 6l10 7 10-7"/></svg>
    sales@trellanstaffing.example.com
  </div>
  <a class="abs menu-btn" href="#" aria-label="Menu">
    <svg width="18" height="14" viewBox="0 0 18 14" stroke="#fff" stroke-width="1.6"><path d="M1 1h16M3 7h12M5 13h8"/></svg>
  </a>
</header>

<section class="section hero">
  <div class="photo hero-photo" role="img" aria-label="Two engineers in hard hats smiling inside a factory hall"></div>
  <h1 class="abs hero-title">Recruiting and Placing Skilled<br>Philippine Workers into<br><span>UK Companies</span></h1>
  <form class="abs form-card">
    <h3>Contact Us Today</h3>
    <div class="field" style="top:100px"><svg width="10" height="12" viewBox="0 0 10 12" fill="#555"><circle cx="5" cy="3" r="3"/><path d="M0 12c0-4 2-5 5-5s5 1 5 5z"/></svg>Name</div>
    <div class="field" style="top:145px"><svg width="12" height="10" viewBox="0 0 12 10" fill="#555"><rect width="12" height="10" rx="1"/><path d="M0 1l6 4 6-4" stroke="#fff" fill="none"/></svg>Email</div>
    <div class="field" style="top:190px"><svg width="11" height="11" viewBox="0 0 24 24" fill="#555"><path d="M22 17v3a2 2 0 0 1-2 2A20 20 0 0 1 2 4a2 2 0 0 1 2-2h3a2 2 0 0 1 2 2l1 3-2 2a16 16 0 0 0 7 7l2-2 3 1a2 2 0 0 1 2 2z"/></svg>Phone</div>
    <div class="field" style="top:233px;height:98px"><svg width="11" height="11" viewBox="0 0 12 12" fill="#555"><rect x="1" y="0" width="10" height="12" rx="1"/><path d="M3 3h6M3 6h6M3 9h4" stroke="#fff"/></svg>Message</div>
    <div class="btn send-btn">Send Message</div>
  </form>
</section>

<section class="section about">
  <div class="photo about-dot"></div>
  <div class="photo about-photo" role="img" aria-label="Two businessmen discussing work at a desk with a laptop"></div>
  <h2 class="abs h2" style="left:633px;top:105px;width:380px">What The Business<br>is About</h2>
  <p>We source skilled workers directly from the Philippines to work in the UK. With offices , training locations and specialist recruiters we can find the highest quality individuals to add value and resources to any UK business. We delivery quality based on vast experience over a number of years.</p>
  <a class="btn" href="#" style="left:633px;top:341px;width:112px;height:37px">Contact Us</a>
</section>

<section class="section working">
  <h2 class="abs h2" style="left:163px;top:133px">Working Together</h2>
  <div class="rule" style="left:163px;top:179px"></div>
  <p>We recruit the finest talent available with our dedicated 200 strong team.<br>Our centres are highlighted in <b>Red Dots</b><br>on the map.</p>
  <a class="btn" href="#" style="left:163px;top:349px;width:110px;height:36px">Contact Us</a>
  <div class="photo map" role="img" aria-label="Map of the Philippines with red dots marking centres in Baguio, Manila, Batangas, Bacolod and Davao"></div>
</section>

<section class="section services">
  <div class="svc-card" style="left:161px">
    <svg width="90" height="90" viewBox="0 0 90 90" fill="none" stroke="#0054AA" stroke-width="2.5"><circle cx="26" cy="20" r="12"/><path d="M26 13v7l5 3"/><rect x="10" y="40" width="34" height="24"/><path d="M6 68h48M27 64v4"/><circle cx="62" cy="36" r="7"/><path d="M50 68v-14a12 12 0 0 1 24 0v14M60 56h22M64 62h18M64 68h18"/></svg>
    <h3>What We Do</h3>
    <p>Our company has been established in the Philippines for over 20 years...</p>
  </div>
  <div class="svc-card" style="left:469px">
    <svg width="90" height="90" viewBox="0 0 90 90" fill="none" stroke="#0054AA" stroke-width="2.5"><path d="M18 44a27 27 0 0 1 54 0"/><rect x="12" y="42" width="12" height="20" rx="5"/><rect x="66" y="42" width="12" height="20" rx="5"/><path d="M72 62c0 10-10 14-22 14"/><rect x="28" y="26" width="34" height="26" rx="10"/><path d="M38 52l-4 8 10-8"/><circle cx="37" cy="39" r="2" fill="#0054AA"/><circle cx="45" cy="39" r="2" fill="#0054AA"/><circle cx="53" cy="39" r="2" fill="#0054AA"/></svg>
    <h3>How We Help</h3>
    <p>We work with companies to find skilled workers that meet the UK requirements for Visas...</p>
  </div>
  <div class="svc-card" style="left:777px">
    <svg width="90" height="90" viewBox="0 0 90 90" fill="none" stroke="#0054AA" stroke-width="2.5"><path d="M74 14c-18 2-32 12-40 30l12 12c18-8 28-22 28-42z"/><circle cx="56" cy="34" r="6"/><path d="M34 44l-12-2-8 10 14 2M46 56l2 12-10 8-2-14M28 62l-14 14M34 68l-8 8M22 56l-8 8"/></svg>
    <h3>Where To Start</h3>
    <p>We need to know what your issues are and how we can understand the personnal you...</p>
  </div>
  <a class="btn" href="#" style="left:543px;top:419px;width:112px;height:35px">Contact Us</a>
</section>

<section class="section placement">
  <h2 class="abs h2 center-title" style="top:82px">Placement We Provide In</h2>
  <div class="rule" style="left:579px;top:131px"></div>
  <a class="arrow-btn" href="#" style="left:98px" aria-label="Previous"><svg width="14" height="10" viewBox="0 0 14 10" fill="none" stroke="#999" stroke-width="1.4"><path d="M13 5H1M5 1L1 5l4 4"/></svg></a>
  <div class="place-tile" style="left:161px;width:274px;background:linear-gradient(135deg,#8fa6bd,#c9d4de 60%,#9aa9b7)" role="img" aria-label="Nurses in a hospital ward">Nursing</div>
  <div class="place-tile" style="left:463px;width:272px;background:linear-gradient(135deg,#2b3f5c,#8f9aa6 55%,#3d4a5c)" role="img" aria-label="Engineer in a yellow hard hat">Engineering</div>
  <div class="place-tile" style="left:763px;width:276px;background:linear-gradient(135deg,#6c7b86,#c7ccd0 55%,#a55f3e)" role="img" aria-label="Welders at work in a workshop">Welding</div>
  <a class="arrow-btn" href="#" style="left:1059px" aria-label="Next"><svg width="14" height="10" viewBox="0 0 14 10" fill="none" stroke="#999" stroke-width="1.4"><path d="M1 5h12M9 1l4 4-4 4"/></svg></a>
  <a class="btn" href="#" style="left:547px;top:433px;width:106px;height:35px">View All</a>
</section>

<section class="section testimonial">
  <div class="abs t-card"></div>
  <div class="photo t-photo" role="img" aria-label="Engineer in a white coat and hard hat standing on a walkway"></div>
  <div class="abs stars">
    <svg width="100" height="18" viewBox="0 0 100 18" fill="#EE7325"><g id="star"><path d="M9 0l2.6 5.6 6.4.7-4.8 4.3 1.4 6.4L9 13.8 3.4 17l1.4-6.4L0 6.3l6.4-.7z"/></g><use href="#star" x="20"/><use href="#star" x="40"/><use href="#star" x="60"/><use href="#star" x="80"/></svg>
  </div>
  <p class="abs t-quote">Lorem ipsum dolor sit amet, consectetur adipiscing elit, sed do eiusmod tempor incididunt ut labore et dolore magna aliqua. Ut enim ad minim veniam, quis nostrud exercitation ullamco laboris nisi...</p>
  <div class="abs t-name">Mara Linwood</div>
  <div class="abs t-role">Engineer</div>
  <div class="abs t-mark">&ldquo;</div>
</section>

<section class="section info">
  <div class="info-card" style="left:161px">
    <div class="info-icon"><svg width="40" height="40" viewBox="0 0 40 40" fill="none" stroke="#0054AA" stroke-width="1.8"><rect x="8" y="6" width="22" height="28" rx="2"/><rect x="14" y="3" width="10" height="6" rx="1"/><path d="M13 16h12M13 22h12M13 28h7"/><circle cx="30" cy="30" r="6"/><path d="M28 30l2 2 3-4"/></svg></div>
    <h3>UK Skilled Workers List</h3>
    <p>The UK government since brexit have developed a new system based on points (similar to Australia)...</p>
    <a class="btn" href="#">Read More</a>
  </div>
  <div class="info-card" style="left:465px">
    <div class="info-icon"><svg width="40" height="40" viewBox="0 0 40 40" fill="none" stroke="#0054AA" stroke-width="1.8"><rect x="8" y="5" width="24" height="30" rx="2"/><circle cx="16" cy="14" r="3"/><path d="M22 12h6M22 16h6M12 22h16M12 27h16"/></svg></div>
    <h3>Sponsor Licence</h3>
    <p>If you have areas of your business that meet the entry requirements of skilled labour your next...</p>
    <a class="btn" href="#">Read More</a>
  </div>
  <div class="info-card" style="left:767px">
    <div class="info-icon"><svg width="40" height="40" viewBox="0 0 40 40" fill="none" stroke="#0054AA" stroke-width="1.8"><circle cx="14" cy="10" r="4"/><path d="M6 32V22a8 8 0 0 1 16 0v10"/><circle cx="28" cy="26" r="8"/><path d="M28 21v5l3 2"/></svg></div>
    <h3>Recruitment Timeline</h3>
    <p>Brief us on the job profiles – this is passed on to our teams in the Philippines...</p>
    <a class="btn" href="#">Read More</a>
  </div>
</section>

<section class="section banner">
  <div class="photo banner-photo" role="img" aria-label="Smiling engineers in blue and orange workwear with hard hats, holding a tablet"></div>
  <h2 class="abs" style="left:163px;top:90px;color:#fff;font-size:32px;font-weight:500">Contact Us Today</h2>
  <div class="rule" style="left:163px;top:138px;background:#fff"></div>
  <p>Please contact us today with your requirements, this can be care workers, chef, welders, pipe fitters, caravan cabinet makers, medical workers. The UK list of required skills is extensive and the Philippines offersenglish speaking highly qualified hard working employees. Contact us today and make that first step to a highly motivated , quality skilled workforce.</p>
  <a class="btn" href="#">Contact Us</a>
</section>

<section class="section quick">
  <h2 class="abs h2 center-title" style="top:84px">Quick Contact</h2>
  <div class="rule" style="left:579px;top:133px"></div>
  <div class="qf" style="left:296px;top:181px"><label>First Name</label><div class="val">Daniel<svg width="14" height="16" viewBox="0 0 14 16" fill="none" stroke="#999"><circle cx="7" cy="4.5" r="3.5"/><path d="M1 15c0-4 3-6 6-6s6 2 6 6z"/></svg></div></div>
  <div class="qf" style="left:614px;top:181px"><label>Last Name</label><div class="val">Hart<svg width="14" height="16" viewBox="0 0 14 16" fill="none" stroke="#999"><circle cx="7" cy="4.5" r="3.5"/><path d="M1 15c0-4 3-6 6-6s6 2 6 6z"/></svg></div></div>
  <div class="qf" style="left:296px;top:267px"><label>Phone</label><div class="val">123 456 7890<svg width="16" height="16" viewBox="0 0 24 24" fill="none" stroke="#999" stroke-width="1.5"><path d="M22 17v3a2 2 0 0 1-2 2A20 20 0 0 1 2 4a2 2 0 0 1 2-2h3a2 2 0 0 1 2 2l1 3-2 2a16 16 0 0 0 7 7l2-2 3 1a2 2 0 0 1 2 2z"/></svg></div></div>
  <div class="qf" style="left:614px;top:267px"><label>Email</label><div class="val">info@danielhart.example.com<svg width="18" height="14" viewBox="0 0 18 14" fill="none" stroke="#999"><rect x=".5" y=".5" width="17" height="13" rx="1"/><path d="M1 1l8 6 8-6"/></svg></div></div>
  <div class="qf" style="left:296px;top:352px;width:610px"><label>Message</label><div class="val" style="padding-bottom:56px">Type Your Message<svg width="18" height="14" viewBox="0 0 18 14" fill="none" stroke="#999"><path d="M2 1h14v9H8l-4 3v-3H2z"/></svg></div></div>
  <a class="btn" href="#" style="left:543px;top:475px;width:112px;height:35px">Submit Now</a>
</section>

<footer class="section site-footer">
  <h4 style="left:161px">Quick Links</h4>
  <a class="f-link" style="left:161px;top:119px;color:#fff;text-decoration:none">›&nbsp; Home</a>
  <a class="f-link" style="left:161px;top:160px;color:#fff;text-decoration:none">›&nbsp; About</a>
  <a class="f-link" style="left:161px;top:203px;color:#fff;text-decoration:none">›&nbsp; Services</a>
  <a class="f-link" style="left:265px;top:119px;color:#fff;text-decoration:none">›&nbsp; Articles</a>
  <a class="f-link" style="left:265px;top:160px;color:#fff;text-decoration:none">›&nbsp; Training</a>
  <a class="f-link" style="left:265px;top:203px;color:#fff;text-decoration:none">›&nbsp; Contact Us</a>

  <h4 style="left:441px">Contact Details</h4>
  <svg class="f-icon" style="top:121px" width="14" height="18" viewBox="0 0 14 18" fill="#fff"><path d="M7 0a7 7 0 0 1 7 7c0 5-7 11-7 11S0 12 0 7a7 7 0 0 1 7-7z"/><circle cx="7" cy="7" r="2.5" fill="#0054AA"/></svg>
  <div class="f-item" style="top:118px">Larkfield Gardens, Seacombe Seacombe<br>HU99 1 United Kingdom</div>
  <svg class="f-icon" style="top:170px" width="16" height="16" viewBox="0 0 24 24" fill="#fff"><path d="M22 17v3a2 2 0 0 1-2 2A20 20 0 0 1 2 4a2 2 0 0 1 2-2h3a2 2 0 0 1 2 2l1 3-2 2a16 16 0 0 0 7 7l2-2 3 1a2 2 0 0 1 2 2z"/></svg>
  <div class="f-item" style="top:168px">07700 900418</div>
  <svg class="f-icon" style="top:200px" width="17" height="13" viewBox="0 0 17 13" fill="#fff"><rect width="17" height="13" rx="1"/><path d="M1 1l7.5 6L16 1" stroke="#0054AA" fill="none"/></svg>
  <div class="f-item" style="top:196px">sales@trellanstaffing.example.com</div>

  <h4 style="left:798px">Follow Us On:</h4>
  <div class="abs" style="left:800px;top:115px;width:140px;height:40px">
    <span class="social" style="left:0"></span>
    <span class="social" style="left:35px"></span>
    <span class="social" style="left:70px"></span>
    <span class="social" style="left:104px"></span>
  </div>
  <div class="abs f-brand">Trellan Staffing</div>
</footer>

<div class="section copy-bar">© 2023 Trellan Staffing Ltd. All Rights Reserved</div>

</body>
</html>
```